New Business Card Design Project

I need a design for business cards, i am an electrical business called "Corvane Electrical and Communications" i need the cards to be double sided with the company logo on the back (attached) the front needs to say my company name, web site, email address, telephone number, and ABN number and electrical license number. I am open to different arrangements of the information but would like the background to be incorporating something electrical or something that looks smart. open to all additional ideas also.

The company colours are orange and grey see logo attached.

Business Name: Corvane Electrical and Communications
Website: corvaneelectricalandcomms.example.com.au
Email: brent@corvaneelectricalandcomms.example.com.au
Telephone(mobile): 0481209736
ABN: 71208349162
Lic No: 418273D

Target Market(s)

Business entities, Project Managers, Accounts, Clients

Industry/Entity Type

Electrician

Contact Information for Business Card

I need a design for business cards, i am an electrical business called "Corvane Electrical and Communications" i need the cards to be double sided with the company logo on the back (attached) the front needs to say my company name

Font styles to use
Serif
Sans Serif

Colors
f37122
5c5c5c

Requirements
Must have
• Must have the Logo on the back open to different ways of it being on the back but had in mind to keep it central but again open to other options
Nice to have
• A real modern cool background that is eye catching yet contemporary
Should not have
• No backgrounds of a light bulb or plug or anything like that

```html
<!DOCTYPE html>
<html lang="en">
<head>
<meta charset="utf-8">
<title>Corvane Electrical and Communications – Business Cards</title>
<link rel="stylesheet" href="https://fonts.googleapis.com/css2?family=Open+Sans:wght@400;600&display=swap">
<style>
  :root {
    --orange: #f9ad19;
    --ink: #1a1a1a;
    --white: #ffffff;
    --backdrop: #e9e6e2;
  }
  * { margin: 0; padding: 0; box-sizing: border-box; }
  html, body { width: 1200px; height: 900px; overflow: hidden; }
  body {
    position: relative;
    background: var(--backdrop);
    font-family: "Open Sans", Arial, sans-serif;
  }
  .card {
    position: absolute;
    overflow: hidden;
    box-shadow: 0 6px 18px rgba(0,0,0,0.18);
  }
  .card-front { left: 77px; top: 33px; width: 589px; height: 365px; background: var(--white); }
  .card-back { left: 388px; top: 505px; width: 567px; height: 352px; background: var(--orange); }
  .front-shapes { position: absolute; inset: 0; }
  .wordmark {
    position: absolute;
    text-align: center;
    font-weight: 600;
    line-height: 1;
  }
  .wordmark-name { display: block; font-size: 50px; letter-spacing: 4px; }
  .wordmark-tag { display: block; font-size: 12.5px; letter-spacing: 1.2px; margin-top: 8px; }
  .card-front .wordmark { left: 0; width: 589px; top: 92px; color: var(--ink); }
  .card-back .wordmark { left: 0; width: 567px; top: 140px; color: var(--white); }
  .contact-list {
    position: absolute;
    right: 226px;
    top: 234px;
    width: 350px;
    list-style: none;
    color: var(--white);
    font-size: 13px;
    letter-spacing: -0.2px;
    text-align: right;
    white-space: nowrap;
  }
  .contact-list li { display: flex; justify-content: flex-end; align-items: center; gap: 9px; height: 25px; }
  .contact-list svg { width: 12px; height: 12px; flex: none; }
  .person {
    position: absolute;
    left: 385px;
    top: 214px;
    color: var(--white);
  }
  .person-name { font-size: 21px; font-weight: 600; line-height: 1.2; }
  .person-role { font-size: 14.5px; line-height: 1.3; }
  .registration { margin-top: 18px; font-size: 15.5px; font-weight: 600; line-height: 1.55; }
</style>
</head>
<body>
  <section class="card card-front" aria-label="Business card front">
    <svg class="front-shapes" width="589" height="365" viewBox="0 0 589 365">
      <polygon points="0,204 382,204 412,168 589,168 589,365 0,365" fill="var(--orange)"/>
      <polygon points="0,176 400,176 378,200 0,200" fill="var(--ink)"/>
    </svg>
    <div class="wordmark">
      <span class="wordmark-name">CORVANE</span>
      <span class="wordmark-tag">ELECTRICAL &amp; COMMUNICATIONS</span>
    </div>
    <ul class="contact-list">
      <li>0481209736
        <svg viewBox="0 0 12 12"><path d="M2.5 1 L4.5 1 L5.3 3.4 L4 4.4 Q5 6.8 7.6 8 L8.6 6.7 L11 7.5 L11 9.5 Q10.5 11 9 11 Q1 10 1 2.5 Q1 1.2 2.5 1Z" fill="var(--white)"/></svg>
      </li>
      <li>brent@corvaneelectricalandcomms.example.com.au
        <svg viewBox="0 0 12 12"><rect x="0.5" y="2" width="11" height="8" fill="var(--white)"/><polyline points="0.8,2.4 6,6.6 11.2,2.4" fill="none" stroke="var(--orange)" stroke-width="1"/></svg>
      </li>
      <li>corvaneelectricalandcomms.example.com.au
        <svg viewBox="0 0 12 12"><circle cx="6" cy="6" r="5.5" fill="var(--white)"/><ellipse cx="6" cy="6" rx="2.3" ry="5.2" fill="none" stroke="var(--orange)" stroke-width="0.8"/><line x1="0.8" y1="6" x2="11.2" y2="6" stroke="var(--orange)" stroke-width="0.8"/></svg>
      </li>
    </ul>
    <div class="person">
      <p class="person-name">Brent Marlow</p>
      <p class="person-role">Director</p>
      <p class="registration">ABN: 71208349162<br>Lic No: 418273D</p>
    </div>
  </section>

  <section class="card card-back" aria-label="Business card back">
    <div class="wordmark">
      <span class="wordmark-name">CORVANE</span>
      <span class="wordmark-tag">ELECTRICAL &amp; COMMUNICATIONS</span>
    </div>
  </section>
</body>
</html>
```